Need webdesign for service company that provides Car hiring service and transit service

We need a web design for a company that provides airport transit services and transport services including Limo, Corporate cars, Disability transit, Family transit service. We need is a simple and professional design.

Below is site which we like and also offer the same service http://www.ridelarkway.com.au/
Updates

Project Deadline Extended
Reason: Waiting for the Feedback from multiple stakeholders. Need the time to select and approve the design

Target Market(s)

Tourism, Travel

Industry/Entity Type

Airport

Number of Pages Required

3 page

Font styles to use
Decorative
Script

Requirements
Must have
• Simple and Professional, Site we like http://www.ridelarkway.com.au/ and also need to mobile friendly
Should not have
• Shouldn't have too many images

```html
<!DOCTYPE html>
<html lang="en">
<head>
<meta charset="utf-8">
<title>Halcyride — Private &amp; Business Transport</title>
<link rel="stylesheet" href="https://fonts.googleapis.com/css2?family=Lato:wght@400;700;900&family=Sorts+Mill+Goudy&display=swap">
<style>
:root{
  --ink:#000;
  --paper:#fff;
  --mist:#f4f4f4;
  --grey-text:#6b6b6b;
  --button:#757073;
  --card-line:#dcdcdc;
  --hero-top:#b9bcbc;
  --hero-mid:#5d6459;
  --hero-low:#3f4040;
}
*{margin:0;padding:0;box-sizing:border-box}
html,body{width:1200px;height:1125px;overflow:hidden;background:var(--paper);font-family:"Lato",sans-serif;color:var(--ink)}
.page{position:relative;width:1200px;height:1125px}
.top-rule{position:absolute;left:0;top:0;width:1200px;height:5px;background:var(--ink)}
.diamond{position:absolute;display:flex;align-items:center;justify-content:center}
.diamond::before{content:"";position:absolute;inset:15%;border:2px solid var(--ink);transform:rotate(45deg);background:var(--paper)}
.diamond svg{position:relative}

.brand{position:absolute;left:101px;top:17px;display:flex;align-items:center}
.brand .diamond{position:relative;width:93px;height:93px}
.brand-text{margin-left:6px}
.brand-name{font-size:40px;font-weight:400;letter-spacing:-1px;line-height:1}
.brand-tag{font-size:10px;font-weight:700;color:var(--grey-text);margin-top:3px;letter-spacing:.2px}

.phone{left:777px;top:39px;width:51px;height:51px}
.phone-number{position:absolute;left:840px;top:51px;font-size:19px;font-weight:700}
.menu-btn{left:989px;top:39px;width:51px;height:51px}
.search-btn{left:1049px;top:39px;width:51px;height:51px}

.intro{position:absolute;left:0;top:129px;width:1200px;height:137px;background:linear-gradient(#efefef,#fbfbfb)}
.intro-title{position:absolute;left:0;right:0;top:28px;text-align:center;font-family:"Sorts Mill Goudy",serif;font-size:34px;line-height:1}
.intro-title .amp{font-size:44px}
.intro-rule{position:absolute;left:419px;width:362px;top:72px;height:1px;background:#555}
.intro-sub{position:absolute;left:0;right:0;top:75px;text-align:center;font-size:20px;color:var(--grey-text)}

.hero{position:absolute;left:0;top:266px;width:1200px;height:552px;background:linear-gradient(180deg,var(--hero-top) 0%,var(--hero-mid) 30%,#4a5146 55%,var(--hero-low) 75%,#6a6a6a 100%)}

.quote{position:absolute;left:751px;top:380px;width:351px;height:325px;background:var(--ink);color:var(--paper)}
.quote h2{position:absolute;top:20px;left:0;right:0;text-align:center;font-size:24px;font-weight:700}
.field{position:absolute;left:20px;width:311px;background:var(--paper);color:var(--ink);display:flex;font-size:12px}
.field .icon{width:33px;border-right:1px solid #ddd;display:flex;align-items:center;justify-content:center}
.field .label{padding-left:13px;display:flex;flex-direction:column;justify-content:center;gap:10px}
.add-stop{display:flex;align-items:center;gap:11px}
.add-stop span.box{width:15px;height:15px;border:1px solid #bbb;display:flex;align-items:center;justify-content:center;font-weight:700;font-size:12px}
.estimate{position:absolute;left:51px;top:258px;width:249px;height:43px;background:var(--button);color:var(--paper);font-size:19px;font-weight:700;display:flex;align-items:center;justify-content:center}

.service{position:absolute;top:818px;width:235px;height:213px;background:var(--paper);border:1px solid var(--card-line);border-top:none;box-shadow:0 6px 6px -4px rgba(0,0,0,.15);text-align:center}
.service .diamond{left:63px;top:-54px;width:108px;height:108px}
.service .diamond::before{border-width:4px;box-shadow:0 2px 4px rgba(0,0,0,.25)}
.service h3{position:absolute;top:84px;left:0;right:0;font-size:17px;font-weight:700}
.service p{position:absolute;top:117px;left:10px;right:10px;font-size:14px;line-height:21px}

.footer{position:absolute;left:0;top:1079px;width:1200px;height:46px;background:var(--ink);color:var(--paper)}
.copyright{position:absolute;left:101px;top:14px;font-size:14px}
.social{top:9px;width:28px;height:28px}
.social::before{border:1.5px solid var(--paper);background:var(--ink)}
</style>
</head>
<body>
<div class="page">
  <div class="top-rule"></div>

  <header>
    <div class="brand">
      <div class="diamond"></div>
      <div class="brand-text">
        <div class="brand-name">HALCYRIDE</div>
        <div class="brand-tag">SMART WAY TO KEEP MOVING</div>
      </div>
    </div>

    <div class="diamond phone" aria-label="Phone">
      <svg width="18" height="18" viewBox="0 0 24 24"><path d="M6.6 10.8a15 15 0 0 0 6.6 6.6l2.2-2.2a1 1 0 0 1 1-.25 11.4 11.4 0 0 0 3.6.6 1 1 0 0 1 1 1V20a1 1 0 0 1-1 1A17 17 0 0 1 3 4a1 1 0 0 1 1-1h3.5a1 1 0 0 1 1 1c0 1.25.2 2.45.6 3.6a1 1 0 0 1-.25 1z"/></svg>
    </div>
    <div class="phone-number">123 456 7890</div>
    <div class="diamond menu-btn" aria-label="Menu">
      <svg width="18" height="16" viewBox="0 0 18 16"><rect y="1" width="18" height="2.6" rx="1"/><rect y="6.7" width="18" height="2.6" rx="1"/><rect y="12.4" width="18" height="2.6" rx="1"/></svg>
    </div>
    <div class="diamond search-btn" aria-label="Search">
      <svg width="18" height="18" viewBox="0 0 18 18" fill="none" stroke="#000" stroke-width="2.2"><circle cx="7.5" cy="7.5" r="5.5"/><path d="M11.5 11.5 16 16" stroke-linecap="round"/></svg>
    </div>
  </header>

  <section class="intro">
    <h1 class="intro-title">Private <span class="amp">&amp;</span> Business</h1>
    <div class="intro-rule"></div>
    <p class="intro-sub">Personalised Transport Services</p>
  </section>

  <section class="hero" role="img" aria-label="Black luxury sedan driving on a mountain road"></section>

  <form class="quote">
    <h2>GET INSTANT QUOTE</h2>
    <div class="field" style="top:71px;height:38px">
      <div class="icon"><svg width="11" height="11"><circle cx="5.5" cy="5.5" r="4.5" fill="none" stroke="#000"/></svg></div>
      <div class="label">Origin ( Public Location Or Exact Address )</div>
    </div>
    <div class="field" style="top:122px;height:38px">
      <div class="icon"><svg width="10" height="14" viewBox="0 0 10 14"><path d="M5 0a5 5 0 0 0-5 5c0 3.5 5 9 5 9s5-5.5 5-9a5 5 0 0 0-5-5zm0 7a2 2 0 1 1 0-4 2 2 0 0 1 0 4z"/></svg></div>
      <div class="label">Destination ( Public Location Or Exact Address )</div>
    </div>
    <div class="field" style="top:175px;height:59px">
      <div class="icon"><svg width="11" height="11"><circle cx="5.5" cy="5.5" r="4.5" fill="none" stroke="#000"/></svg></div>
      <div class="label">
        <span>Show other vehicles</span>
        <span class="add-stop"><span class="box">+</span>Add Stops</span>
      </div>
    </div>
    <div class="estimate">ESTIMATE FARE</div>
  </form>

  <article class="service" style="left:99px">
    <div class="diamond">
      <svg width="56" height="28" viewBox="0 0 56 28"><path d="M4 14 14 13l8-8h14l9 8 7 1 2 8H2z"/><circle cx="14" cy="22" r="5" fill="#fff" stroke="#000" stroke-width="3"/><circle cx="42" cy="22" r="5" fill="#fff" stroke="#000" stroke-width="3"/><path d="M24 7h5v6h-11zM31 7h4l6 6H31z" fill="#fff"/></svg>
    </div>
    <h3>CORPORATE CARS</h3>
    <p>Lorem ipsum dolor sit amet conse adipiscing elit maecena commod sem neciscin...[+]</p>
  </article>

  <article class="service" style="left:355px">
    <div class="diamond">
      <svg width="42" height="32" viewBox="0 0 42 32"><path d="M8 2h26l4 10h4v4h-2v16h-6v-4H8v4H2V16H0v-4h4z"/><path d="M10 5h22l3 7H7z" fill="#fff"/><rect x="14" y="17" width="14" height="8" fill="#fff"/><path d="M16 18v6M19 18v6M22 18v6M25 18v6" stroke="#000"/></svg>
    </div>
    <h3>LIMO SERVICE</h3>
    <p>Lorem ipsum dolor sit amet conse adipiscing elit maecena commod sem neciscin...[+]</p>
  </article>

  <article class="service" style="left:609px">
    <div class="diamond">
      <svg width="44" height="42" viewBox="0 0 44 42"><circle cx="14" cy="5" r="4"/><path d="M11 11h5v10h10l4 10 5-2 1 3-8 3-5-10H11z"/><path d="M8 18a12 12 0 1 0 18 14" fill="none" stroke="#000" stroke-width="3.5"/></svg>
    </div>
    <h3>DISABILITY TRANSIT</h3>
    <p>Lorem ipsum dolor sit amet conse adipiscing elit maecena commod sem neciscin...[+]</p>
  </article>

  <article class="service" style="left:866px">
    <div class="diamond">
      <svg width="50" height="40" viewBox="0 0 50 40"><path d="M4 2h24a2 2 0 0 1 2 2v30h-4v5h-5v-5H11v5H6v-5H2V4a2 2 0 0 1 2-2z"/><rect x="6" y="8" width="20" height="10" fill="#fff"/><circle cx="8" cy="27" r="2" fill="#fff"/><circle cx="24" cy="27" r="2" fill="#fff"/><circle cx="37" cy="20" r="2.5"/><path d="M34 24h6v8h-1v7h-4v-7h-1z"/><circle cx="45" cy="24" r="2"/><path d="M43 27h4v6h-1v6h-2v-6h-1z"/></svg>
    </div>
    <h3>FAMILY TRANSIT SERVICE</h3>
    <p>Lorem ipsum dolor sit amet conse adipiscing elit maecena commod sem neciscin...[+]</p>
  </article>

  <footer class="footer">
    <p class="copyright">Copyright © 2017 HALCYRIDE. All Rights Reserved.</p>
    <a class="diamond social" style="left:1005px" aria-label="Social link one"></a>
    <a class="diamond social" style="left:1038px" aria-label="Social link two"></a>
    <a class="diamond social" style="left:1072px" aria-label="Social link three"></a>
  </footer>
</div>
</body>
</html>
```